Kestrel Home Business Card Design

We need a business card for a Building company based in Queensland, Australia. Our colours are orange black and we do base all our homes design names and other aspect of our business on astrology. We want the consumer to perceive the company as professional and to attract investors to our company.We have over 20 years in the building industry.We pride ourselves on our innovation of designs and making the building process for anyone from families to investor a smooth and simple experience.
Business
Amelia Prichard0411752116PO Box 454, Mudgeerbaameliaprichard@zodiachomes.com

```html
<!DOCTYPE html>
<html lang="en">
<head>
<meta charset="utf-8">
<title>Kestrel Homes – Business Card</title>
<link href="https://fonts.googleapis.com/css2?family=Open+Sans:wght@400;600;700&display=swap" rel="stylesheet">
<style>
  :root {
    --backdrop: #2c2e33;
    --orange: #f0901e;
    --orange-soft: rgba(255, 255, 255, 0.2);
    --card-white: #f6f6f6;
    --ink: #1c1c1c;
    --ink-soft: #333;
    --rule: #cfcfcf;
    --paper: #ffffff;
  }
  * { box-sizing: border-box; margin: 0; padding: 0; }
  html, body {
    width: 1200px;
    height: 864px;
    overflow: hidden;
    background: var(--backdrop);
    font-family: "Open Sans", Arial, sans-serif;
  }
  .card {
    position: absolute;
    width: 560px;
    height: 320px;
    border-radius: 3px;
    box-shadow: 0 10px 24px rgba(0, 0, 0, 0.35);
    overflow: hidden;
  }

  /* Front */
  .card-front {
    left: 180px;
    top: 60px;
    background: var(--orange);
  }
  .front-disc {
    position: absolute;
    left: 140px;
    top: 20px;
    width: 280px;
    height: 280px;
    border-radius: 50%;
    background: var(--orange-soft);
  }
  .front-name {
    position: absolute;
    inset: 0;
    display: flex;
    align-items: center;
    justify-content: center;
    color: var(--paper);
    font-weight: 700;
    font-size: 34px;
    letter-spacing: 0.5px;
  }

  /* Back */
  .card-back {
    left: 460px;
    top: 470px;
    background: linear-gradient(135deg, var(--paper) 0%, var(--card-white) 100%);
  }
  .holder {
    position: absolute;
    left: 32px;
    top: 92px;
  }
  .holder-name {
    font-size: 22px;
    font-weight: 600;
    color: var(--ink-soft);
    line-height: 1.15;
  }
  .holder-role {
    font-size: 14px;
    color: var(--orange);
    line-height: 1.3;
  }
  .divider {
    position: absolute;
    left: 175px;
    right: 28px;
    top: 148px;
    height: 1px;
    background: var(--rule);
  }
  .brand {
    position: absolute;
    right: 28px;
    top: 26px;
    display: flex;
    flex-direction: column;
    align-items: center;
    gap: 14px;
  }
  .brand-dot {
    width: 50px;
    height: 50px;
    border-radius: 50%;
    background: var(--orange);
  }
  .brand-name {
    font-size: 26px;
    font-weight: 700;
    color: var(--ink);
    letter-spacing: 0.2px;
  }
  .contacts {
    position: absolute;
    right: 28px;
    top: 168px;
    list-style: none;
  }
  .contacts li {
    display: flex;
    align-items: center;
    justify-content: flex-end;
    gap: 10px;
    height: 23px;
    font-size: 15px;
    color: var(--ink);
    white-space: nowrap;
  }
  .icon {
    width: 17px;
    height: 17px;
    border-radius: 2px;
    background: var(--orange);
    display: flex;
    align-items: center;
    justify-content: center;
    flex: none;
  }
  .icon svg { width: 11px; height: 11px; }
</style>
</head>
<body>

<section class="card card-front" aria-label="Card front">
  <div class="front-disc"></div>
  <div class="front-name">Kestrel Homes</div>
</section>

<section class="card card-back" aria-label="Card back">
  <div class="holder">
    <p class="holder-name">Harriet Colvane</p>
    <p class="holder-role">Managing Director</p>
  </div>

  <div class="brand">
    <div class="brand-dot"></div>
    <p class="brand-name">Kestrel Homes</p>
  </div>

  <div class="divider"></div>

  <ul class="contacts">
    <li>07-5530-4418
      <span class="icon"><svg viewBox="0 0 12 12" fill="#fff"><path d="M2 1h2.5l1 2.5-1.5 1a6 6 0 0 0 3.5 3.5l1-1.5 2.5 1V10a1 1 0 0 1-1 1A9 9 0 0 1 1 2a1 1 0 0 1 1-1z"/></svg></span>
    </li>
    <li>07-5530-4419
      <span class="icon"><svg viewBox="0 0 12 12" fill="#fff"><rect x="3" y="1" width="6" height="3"/><rect x="1" y="4" width="10" height="5" rx="1"/><rect x="3" y="8" width="6" height="3" fill="#fff" stroke="#f0901e" stroke-width="0.8"/></svg></span>
    </li>
    <li>0487-309-625
      <span class="icon"><svg viewBox="0 0 12 12" fill="none" stroke="#fff" stroke-width="1.3"><rect x="3" y="0.8" width="6" height="10.4" rx="1"/><line x1="5" y1="9.2" x2="7" y2="9.2"/></svg></span>
    </li>
    <li>harrietcolvane@kestrelhomes.example
      <span class="icon"><svg viewBox="0 0 12 12" fill="none" stroke="#fff" stroke-width="1.2"><rect x="1" y="2.5" width="10" height="7"/><path d="M1 2.5l5 4 5-4"/></svg></span>
    </li>
    <li>www.kestrelhomes.example
      <span class="icon"><svg viewBox="0 0 12 12" fill="none" stroke="#fff" stroke-width="1.4" stroke-linecap="round"><path d="M5 7l2-2"/><path d="M6.5 3.5l1-1a2 2 0 0 1 2.8 2.8l-1 1"/><path d="M5.5 8.5l-1 1a2 2 0 0 1-2.8-2.8l1-1"/></svg></span>
    </li>
  </ul>
</section>

</body>
</html>
```